Post Card Design - Photo on front, details on back. Logo on both sides.

Back: See the photo of my old card. The back worked well, as it gave me lots of space to write on. The address details are still correct, but the logo has changed to Josephine Sans. Logo can be on one line or on two (if two, align it on the left).
Don't include the 'BEAUTIFUL WEDDING DRESSES...' bit.
I'd like to print this on thicker, slightly coarse paper, so don't go too small on detail.
Here are the Trelo paper details: Paper Stock: Natural Uncoated
Paper Thickness: Premium
Finish: None
Front of Card: I'd like to see options for both pictures:
I think the painted image would look best with a frame in a pale shade and the logo in the frame fairly subtle.
The actual dress photo I'd like to see cropped a bit like in my mock up. You'll need to have a look at how the logo would be best placed on this. You can place it anywhere, or add a banner.
See my website for my brand's look: mirelhoffkin.co.nz
Target Market(s)
Brides
Industry/Entity Type
Wedding Dresses
Contact Information for Business Card
Front: Photo and logo. Back: with details and lots of empty space. See attached photos for loose brief.
Other font styles liked:
- Josephine Sans
Requirements
Must have
- I hand-write the gown designs and price on the back of the card, so there needs to be plenty of empty space.
Nice to have
- As per brief.
Should not have
- It must look clean, romantic, modern. Timeless.

```html
<!DOCTYPE html>
<html lang="en">
<head>
<meta charset="utf-8">
<title>Mirel Hoffkin — Post Card</title>
<link rel="stylesheet" href="https://fonts.googleapis.com/css2?family=Josefin+Sans:wght@300;400&family=Nunito+Sans:wght@300;400&display=swap">
<style>
  :root {
    --backdrop: #ecebea;
    --card-white: #fbfbfa;
    --band-grey: #b7b8bb;
    --ink: #2b2b2d;
    --ink-soft: #3e3f43;
    --logo-light: #ffffff;
    --photo-light: #f1e7d6;
    --photo-mid: #dccab0;
    --photo-deep: #bda684;
    --shadow: rgba(0, 0, 0, 0.12);
  }
  * { margin: 0; padding: 0; box-sizing: border-box; }
  html, body {
    width: 1200px;
    height: 900px;
    overflow: hidden;
    background: var(--backdrop);
    font-family: "Josefin Sans", sans-serif;
  }
  .canvas { position: relative; width: 1200px; height: 900px; }

  .card {
    position: absolute;
    width: 552px;
    height: 367px;
    box-shadow: 1px 2px 4px var(--shadow);
    overflow: hidden;
  }

  /* Front */
  .card-front { left: 137px; top: 80px; }
  .front-photo {
    position: absolute;
    inset: 0;
    background:
      radial-gradient(ellipse at 75% 70%, var(--photo-light) 0%, transparent 55%),
      linear-gradient(160deg, var(--photo-mid) 0%, var(--photo-light) 45%, var(--photo-mid) 70%, var(--photo-deep) 100%);
  }
  .front-logo {
    position: absolute;
    left: 40px;
    bottom: 36px;
    color: var(--logo-light);
    font-size: 28px;
    font-weight: 300;
    letter-spacing: 4px;
    text-transform: uppercase;
    white-space: nowrap;
  }

  /* Back */
  .card-back { left: 521px; top: 474px; background: var(--card-white); }
  .back-logo {
    position: absolute;
    left: 53px;
    top: 53px;
    font-size: 25px;
    font-weight: 300;
    letter-spacing: 1.6px;
    color: var(--ink);
    text-transform: uppercase;
  }
  .contact-band {
    position: absolute;
    left: 0;
    right: 0;
    bottom: 0;
    height: 56px;
    background: var(--band-grey);
    display: flex;
    align-items: center;
    justify-content: flex-end;
    gap: 14px;
    padding-right: 32px;
  }
  .contact-item {
    display: flex;
    align-items: center;
    gap: 3px;
    font-family: "Nunito Sans", sans-serif;
    font-size: 14px;
    font-weight: 400;
    color: var(--ink-soft);
    white-space: nowrap;
  }
  .contact-item svg { width: 11px; height: 11px; flex: none; }
</style>
</head>
<body>
<main class="canvas">

  <section class="card card-front" aria-label="Post card front">
    <div class="front-photo" role="img" aria-label="Photograph of a bride in a flowing ivory gown in a sunlit stone hallway"></div>
    <h1 class="front-logo">Mirel Hoffkin</h1>
  </section>

  <section class="card card-back" aria-label="Post card back">
    <h2 class="back-logo">Mirel Hoffkin</h2>
    <div class="contact-band">
      <span class="contact-item">
        <svg viewBox="0 0 12 12" aria-hidden="true"><path d="M3 1.2 4.6 3.4 3.7 4.6c.7 1.5 1.9 2.7 3.4 3.4l1.2-.9 2.2 1.6-.8 1.9C5.5 10.6 1.4 6.5 1.1 2z" fill="none" stroke="currentColor" stroke-width="1"/></svg>
        +64 9 555 0147
      </span>
      <span class="contact-item">
        <svg viewBox="0 0 12 12" aria-hidden="true"><g fill="none" stroke="currentColor" stroke-width="0.9"><circle cx="6" cy="6" r="5"/><ellipse cx="6" cy="6" rx="2.2" ry="5"/><path d="M1 6h10M1.8 3.5h8.4M1.8 8.5h8.4"/></g></svg>
        mirelhoffkin.co.nz
      </span>
      <span class="contact-item">
        <svg viewBox="0 0 12 12" aria-hidden="true"><g fill="none" stroke="currentColor" stroke-width="1"><rect x="1" y="2.5" width="10" height="7"/><path d="M1 2.5 6 6.5l5-4"/></g></svg>
        mire@mirelhoffkin.co.nz
      </span>
    </div>
  </section>

</main>
</body>
</html>
```